Velmori Sciences needs high end Label Design for a revolutionary new supplement

We at Velmori Sciences are looking for a brand new Label Design for a first of its kind product called Solvenna. It is the first supplement on the market that treats grief and heartbreak. This product is unisex for both men and woman. We want the New Label to look high end and luxurious using the brand colors which are gold and burgundy. Please feel free to use other colors such as black, white, or gray to go along with it or any other colors if you feel would be a great fit! Velmori Sciences is like the Tarnwick of the supplement world, coming out with new products that will challenge the way people treat different symptoms. To Recap:

1. Product Name: SOLVENNA - the font will play a big roll
2. The Label will be placed on an all white bottle
3. Some parts of the label will be printed with foil to make parts of the label shiny and more attractive. Please keep this in mind when designing.
4. Must use our Logo. I will attach a file of our logo and of the emblem as well. Feel free to use the emblem separately if you have a great idea for it. Please let us know if you need the Logo in a different file type.
5. This all natural herbal supplement in pill form is the first to treat grief and support someone with a broken heart. The consumers purchasing this product will be going through a hard and emotional time. This is a serious product.
6. The manufacturer has included some basic instructions regarding the dye line and file types. Please do your best to meet these. If you cannot meet the guidelines please submit art work anyways. If your design is chosen we will just have the manufacturer replicate the design.

The final label should portray Solvenna and Velmori Sciences as a luxurious brand and product which was made with cutting edge science leading the way with revolutionary ideas. We want customers to feel that the product is worth every penny, because it is. As soon as they receive the product and take one look at the label, I want them to think WOW I made the right choice buying this. I have attached some Label designs that we really liked for your review.

Please feel free to message me with any questions or if you need the Logo in a different file type. Thank you all.
Updates

Please send in more entries while we take a couple days to review, we are still looking for that one design we can work with. We are getting close, thank you all!

Target Market(s)

People going through grief and heartbreak.

Font styles to use
Sans Serif
Script
Other font styles liked:
• Any font that looks good, The font for the name SOLVENNA is very important and will brand it. We hated the font used in the label we received in our first label draft (attached so you can see)

Requirements
Must have
• Must have the company Logo that says the company name
• Must have the colors Gold and Burgundy
• Must have some areas that will be the shiny foil when label is printed.
• Must say "Dietary Supplement" somewhere near the bottom along with "90 Capsules"
• I have attached a Label someone designed for us but were not really happy with. I did like the font the "Dietary supplement" and "90 Capsules" had and also where it was placed. We absolutely HATED the font used for Solvenna.
• Must look at the label design we received from the manufacturer and take into consideration the room needed to write in the directions and all the symbols such as "made in america" and "KMT Facility" Don't worry about adding these in as they will put those in before printing but keep in mind they will be added to the Final Label along with the Supplement Facts.
Nice to have
• Would like to see other colors to go with gold and burgundy suck as black, white, or gray. I have attached some Label designs that I really liked for your reference.
Should not have
• Does not need to have any other legal language, that will be applied by the the manufacturer's graphics team.

```html
<!DOCTYPE html>
<html lang="en">
<head>
<meta charset="utf-8">
<title>Solvenna – Velmori Sciences Label</title>
<link rel="stylesheet" href="https://fonts.googleapis.com/css2?family=Cinzel:wght@500&family=Montserrat:wght@500;700&family=Russo+One&display=swap">
<style>
  :root {
    --backdrop: #f4f4f6;
    --indigo: #2a2474;
    --indigo-deep: #1d1958;
    --panel-black: #0c0a0b;
    --gold: #d8a94e;
    --gold-light: #fbe3a2;
    --gold-dark: #8c5a1c;
    --burgundy: #b01e2a;
    --ink-light: #efe6d6;
  }
  * { box-sizing: border-box; margin: 0; padding: 0; }
  html, body {
    width: 1200px;
    height: 1200px;
    overflow: hidden;
    background: var(--backdrop);
  }
  .canvas {
    position: relative;
    width: 1200px;
    height: 1200px;
  }
  .label {
    position: absolute;
    left: 40px;
    top: 80px;
    width: 1120px;
    height: 1040px;
    background: linear-gradient(180deg, var(--indigo) 0%, var(--indigo-deep) 100%);
    overflow: hidden;
  }
  .label-shimmer {
    position: absolute;
    inset: 0;
    background:
      radial-gradient(ellipse 300px 420px at 92% 72%, rgba(216,169,78,0.28), transparent 70%),
      radial-gradient(ellipse 260px 200px at 24% 14%, rgba(216,169,78,0.18), transparent 70%),
      radial-gradient(ellipse 200px 240px at 20% 80%, rgba(216,169,78,0.14), transparent 70%);
  }
  .brand-panel {
    position: absolute;
    left: 280px;
    top: 240px;
    width: 560px;
    height: 560px;
    background: var(--panel-black);
    border: 3px solid var(--gold);
    box-shadow: inset 0 0 0 2px var(--gold-dark);
    text-align: center;
  }
  .company {
    position: absolute;
    top: 62px;
    left: 0;
    right: 0;
    display: flex;
    flex-direction: column;
    align-items: center;
  }
  .company-dot {
    width: 64px;
    height: 64px;
    border-radius: 50%;
    background: var(--burgundy);
    margin-bottom: 18px;
  }
  .company-name {
    font-family: "Cinzel", serif;
    font-weight: 500;
    font-size: 36px;
    line-height: 1.1;
    letter-spacing: 3px;
    color: var(--gold);
  }
  .product-name {
    position: absolute;
    top: 262px;
    left: 50%;
    transform: translateX(-50%);
    white-space: nowrap;
    font-family: "Russo One", sans-serif;
    font-size: 96px;
    letter-spacing: 3px;
    line-height: 1;
    background: linear-gradient(180deg, var(--gold-light) 0%, var(--gold) 45%, var(--gold-dark) 55%, var(--gold) 100%);
    -webkit-background-clip: text;
    background-clip: text;
    color: transparent;
    filter: drop-shadow(0 4px 3px rgba(0,0,0,0.7));
  }
  .panel-rule {
    position: absolute;
    left: 50px;
    right: 50px;
    top: 456px;
    height: 2px;
    background: var(--gold);
  }
  .supplement-line {
    position: absolute;
    top: 474px;
    left: 0;
    right: 0;
    display: flex;
    justify-content: center;
    align-items: baseline;
    gap: 12px;
    font-family: "Montserrat", sans-serif;
    font-weight: 500;
    font-size: 20px;
    letter-spacing: 1px;
    color: var(--ink-light);
  }
  .capsule-count {
    font-weight: 700;
    font-size: 40px;
    color: var(--gold);
  }
</style>
</head>
<body>
  <main class="canvas">
    <section class="label">
      <div class="label-shimmer"></div>
      <div class="brand-panel">
        <div class="company">
          <span class="company-dot"></span>
          <p class="company-name">VELMORI<br>SCIENCES</p>
        </div>
        <h1 class="product-name">SOLVENNA</h1>
        <div class="panel-rule"></div>
        <p class="supplement-line">
          <span>DIETARY SUPPLEMENT</span>
          <span class="capsule-count">90</span>
          <span>CAPSULES</span>
        </p>
      </div>
    </section>
  </main>
</body>
</html>
```